Business Card Design Project

Business Card
We are rebranding with a new logo
Industry/Entity Type
Business
Contact Information for Business Card
Dennis Morvale +61 487215963 dennis@quorv.com.au P.O. Box 872 Fernlow QLD 4309
Requirements
Must have
- Logo

```html
<!DOCTYPE html>
<html lang="en">
<head>
<meta charset="utf-8">
<title>Quorv International – Business Card</title>
<link rel="stylesheet" href="https://fonts.googleapis.com/css2?family=Roboto:wght@400;500;700&display=swap">
<style>
  :root {
    --backdrop: #5f5a55;
    --card-white: #ffffff;
    --card-dark: #1c1d1f;
    --blue-bright: #1b9ad4;
    --blue-mid: #136e9a;
    --blue-deep: #0d4e70;
    --text-grey: #4a4a4a;
  }
  * { margin: 0; padding: 0; box-sizing: border-box; }
  html, body {
    width: 1200px; height: 960px; overflow: hidden;
    background: var(--backdrop);
    font-family: "Roboto", Arial, sans-serif;
  }
  .card {
    position: absolute;
    left: 315px; top: 294px;
    width: 600px; height: 342px;
    border-radius: 18px;
    background: var(--card-white);
    overflow: hidden;
  }
  .card-art { position: absolute; inset: 0; }
  .brand {
    position: absolute;
    left: 42px; top: 150px;
    width: 230px;
    color: var(--blue-bright);
    font-weight: 500;
    text-align: center;
  }
  .brand-name { font-size: 50px; letter-spacing: 2px; line-height: 1; }
  .brand-tagline { font-size: 20px; letter-spacing: 2.5px; margin-top: 14px; }
  .holder-name {
    position: absolute;
    right: 28px; top: 26px;
    color: var(--blue-bright);
    font-size: 20px; font-weight: 500;
  }
  .details {
    position: absolute;
    right: 28px; top: 213px;
    color: var(--text-grey);
    font-size: 14px; line-height: 18px;
    text-align: right;
  }
  .address { margin-right: 0; margin-bottom: 8px; }
  .contact-line {
    display: flex; justify-content: flex-end; align-items: center; gap: 8px;
    height: 19.5px;
  }
  .contact-icon { width: 13px; height: 13px; fill: var(--blue-bright); }
</style>
</head>
<body>
  <div class="card">
    <svg class="card-art" viewBox="0 0 600 342" preserveAspectRatio="none" aria-hidden="true">
      <path d="M120,0 C330,10 400,60 388,112 C370,190 305,262 252,342 H0 V0 Z" fill="var(--blue-bright)"/>
      <path d="M120,0 C310,14 372,62 362,112 C346,188 290,262 250,342 H0 V0 Z" fill="var(--blue-mid)"/>
      <path d="M120,0 C290,18 350,64 340,112 C324,186 280,262 246,342 H0 V0 Z" fill="var(--blue-deep)"/>
      <path d="M120,0 C270,22 330,66 320,112 C306,184 272,262 244,342 H0 V0 Z" fill="var(--card-dark)"/>
    </svg>

    <div class="brand">
      <div class="brand-name">QUORV</div>
      <div class="brand-tagline">INTERNATIONAL</div>
    </div>

    <div class="holder-name">DENNIS MORVALE</div>

    <div class="details">
      <p class="address">P.O. Box 872<br>Fernlow QLD 4309</p>
      <p class="contact-line">+61 487215963
        <svg class="contact-icon" viewBox="0 0 16 16"><path d="M3.5 1 L6 1 L7 4.5 L5.3 6 C6.2 8 8 9.8 10 10.7 L11.5 9 L15 10 L15 12.5 C15 13.9 13.9 15 12.5 15 C6.2 15 1 9.8 1 3.5 C1 2.1 2.1 1 3.5 1 Z"/></svg>
      </p>
      <p class="contact-line">dennis@quorv.com.au
        <svg class="contact-icon" viewBox="0 0 16 16"><path d="M1 3 H15 V4 L8 9 L1 4 Z M1 5.5 L8 10.5 L15 5.5 V13 H1 Z"/></svg>
      </p>
      <p class="contact-line">www.quorv.com.au
        <svg class="contact-icon" viewBox="0 0 16 16"><circle cx="8" cy="8" r="7"/><path d="M1.5 8 H14.5 M8 1.2 C5 4 5 12 8 14.8 M8 1.2 C11 4 11 12 8 14.8" stroke="#fff" stroke-width="1.1" fill="none"/></svg>
      </p>
    </div>
  </div>
</body>
</html>
```